Upmarket Dessert Lounge needs a Business Card Design

We are an upmarket dessert lounge needing a business card to match our image.

We want something that is simple yet beautiful, feminine, classy, sophisticated and elegant. We want it to stand out and don't mind if it is bold.

The design should include our logo and colours of red or maroon with gold highlights. We don't mind if black is used.

Marlow & Quince

Target Market(s)

For those who like to indulge or treat themselves and give in to their temptations on good quality desserts.

Industry/Entity Type

Business

Requirements
Must have
• Must include our logo and our name

Marlow & Quince

M & Q

```html
<!DOCTYPE html>
<html lang="en">
<head>
<meta charset="utf-8">
<title>Marlow &amp; Quince — Business Card</title>
<link rel="stylesheet" href="https://fonts.googleapis.com/css2?family=Libre+Baskerville&display=swap">
<style>
  :root {
    --page-bg: #e9e6e2;
    --card-red: #862a24;
    --card-red-deep: #7a241f;
    --gold: #f2d5a2;
    --gold-soft: #d9b57e;
  }
  html, body {
    margin: 0;
    width: 1200px;
    height: 960px;
    overflow: hidden;
    background: var(--page-bg);
  }
  .canvas {
    position: relative;
    width: 1200px;
    height: 960px;
  }
  .card {
    position: absolute;
    left: 250px;
    width: 700px;
    height: 400px;
    background: var(--card-red);
    box-shadow: 0 6px 18px rgba(0,0,0,0.18);
    font-family: "Libre Baskerville", Georgia, serif;
    color: var(--gold);
  }
  .card--front { top: 60px; }
  .card--back  { top: 500px; }

  .flourish {
    position: absolute;
    left: 275px;
    top: 32px;
    width: 150px;
    height: 52px;
    border-radius: 26px;
    background: linear-gradient(90deg, rgba(242,213,162,0.25), rgba(242,213,162,0.75), rgba(242,213,162,0.25));
  }
  .holder {
    position: absolute;
    top: 122px;
    left: 0;
    width: 100%;
    text-align: center;
  }
  .holder__name {
    margin: 0;
    font-size: 32px;
    font-weight: 400;
    letter-spacing: 0.3px;
  }
  .holder__role {
    margin: 8px 0 0;
    font-size: 17px;
  }
  .divider {
    position: absolute;
    left: 110px;
    top: 226px;
    width: 480px;
    height: 2px;
    background: linear-gradient(90deg, transparent, var(--gold-soft) 50%, transparent);
  }
  .contacts {
    position: absolute;
    left: 70px;
    top: 262px;
    margin: 0;
    padding: 0;
    list-style: none;
    font-size: 19px;
    line-height: 30px;
  }
  .contacts li {
    display: flex;
    align-items: center;
    gap: 14px;
  }
  .contacts svg {
    width: 18px;
    height: 18px;
    flex: none;
  }
  .address {
    position: absolute;
    left: 410px;
    top: 248px;
    margin: 0;
    font-style: normal;
    font-size: 16px;
    line-height: 26px;
  }
  .brand {
    position: absolute;
    inset: 0;
    display: flex;
    align-items: center;
    justify-content: center;
    gap: 18px;
  }
  .brand__dot {
    width: 14px;
    height: 14px;
    border-radius: 50%;
    background: var(--gold);
  }
  .brand__name {
    margin: 0;
    font-size: 46px;
    font-weight: 400;
    letter-spacing: 2px;
    color: var(--gold);
    text-transform: uppercase;
  }
</style>
</head>
<body>
<main class="canvas">

  <section class="card card--front" aria-label="Business card front">
    <div class="flourish" role="img" aria-label="Gold decorative flourish"></div>
    <div class="holder">
      <h1 class="holder__name">Name Surname</h1>
      <p class="holder__role">Manager</p>
    </div>
    <div class="divider"></div>
    <ul class="contacts">
      <li>
        <svg viewBox="0 0 18 18" aria-hidden="true" fill="none" stroke="currentColor" stroke-width="1.6">
          <rect x="3" y="1.5" width="12" height="15" rx="1.5"/>
          <rect x="6" y="4" width="6" height="3"/>
          <path d="M6 10h1M9 10h1M12 10h0.5M6 13h1M9 13h1M12 13h0.5"/>
        </svg>
        (221) 33 471 20 48
      </li>
      <li>
        <svg viewBox="0 0 18 18" aria-hidden="true" fill="none" stroke="currentColor" stroke-width="1.6">
          <rect x="5" y="2" width="8" height="4"/>
          <rect x="2" y="6" width="14" height="7" rx="1"/>
          <rect x="5" y="11" width="8" height="5" fill="currentColor"/>
        </svg>
        (221) 33 471 20 49
      </li>
      <li>
        <svg viewBox="0 0 18 18" aria-hidden="true" fill="none" stroke="currentColor" stroke-width="1.6">
          <rect x="2" y="4" width="14" height="10"/>
          <path d="M2 4l7 6 7-6M2 14l5-5M16 14l-5-5"/>
        </svg>
        hello@marlow-quince.com
      </li>
    </ul>
    <address class="address">
      Rue des Tilleuls - Belle Vue<br>
      BP 512 - City, Country<br>
      www.marlow-quince.com
    </address>
  </section>

  <section class="card card--back" aria-label="Business card back">
    <div class="brand">
      <span class="brand__dot"></span>
      <p class="brand__name">Marlow &amp; Quince</p>
    </div>
  </section>

</main>
</body>
</html>
```